Business card design for new eCommerce site focusing on integrity and strong businsess tactics

We need a business card that will stand out and be memorable. Something with color that matches our company logo colors. Think high end version of Pactivo. There are 2 logos provided. The parent company is called Amber Ledge Partners and we are presenting a new and very exciting eCommerce site called BrightHarborTrade.example.

Target Market(s)

Our target markets are in the Activities, Food and Beverage, Health and Beauty

Industry/Entity Type

Marketing

Contact Information for Business Card

We have 4 members that need cards...I will provide all info to the winner of the design contest
Business Address is
4870 West 63rd Avenue, Suite C207
Phoenix AZ 85731

Font styles to use
Serif
Sans Serif

Colors

Designer to choose colors to be used in the design.

Requirements
Must have
• The card must be memorable...should be unique in design but must exude integrity and be playful .
• I have provided several colors or our parent company...please feel free to use which ever
Nice to have
• I will leave this up to you. Feel free to use other images of your choosing that wraps around our client.....Activities, Dining, Health, Beauty
Should not have
• just dont be boring

```html
<!DOCTYPE html>
<html lang="en">
<head>
<meta charset="utf-8">
<title>BrightHarborTrade.example – Business Card</title>
<link rel="stylesheet" href="https://fonts.googleapis.com/css2?family=Jost:wght@400;500;600;700&display=swap">
<style>
  :root {
    --backdrop: #2a2a2a;
    --card-white: #f7f7f5;
    --brand-blue: #2e86c1;
    --brand-green: #8cc63f;
    --lime-light: #b9e152;
    --lime-deep: #76bf2f;
    --navy: #13214d;
    --text-grey: #4a4a4a;
    --muted-grey: #666;
  }
  * { margin: 0; padding: 0; box-sizing: border-box; }
  html, body {
    width: 1200px; height: 960px; overflow: hidden;
    background: var(--backdrop);
    font-family: "Jost", sans-serif;
  }
  .card {
    position: absolute;
    width: 600px; height: 342px;
    border-radius: 18px;
    overflow: hidden;
  }
  .card-front { left: 302px; top: 131px; background: var(--card-white); }
  .card-back {
    left: 299px; top: 490px;
    background: linear-gradient(135deg, var(--lime-light) 0%, var(--lime-deep) 55%, var(--lime-deep) 100%);
  }
  .corner-swoosh { position: absolute; left: 0; top: 0; width: 600px; height: 342px; }

  .brand-lockup { position: absolute; left: 292px; top: 38px; display: flex; align-items: center; gap: 8px; }
  .brand-dot { width: 16px; height: 16px; border-radius: 50%; background: var(--brand-blue); }
  .brand-name { font-size: 23px; font-weight: 500; color: var(--brand-green); letter-spacing: -0.2px; }
  .brand-tagline {
    position: absolute; left: 316px; top: 84px;
    font-size: 11.5px; color: var(--muted-grey); letter-spacing: 1.1px;
  }

  .contact-block { position: absolute; left: 35px; top: 144px; color: var(--text-grey); }
  .person-name { font-size: 23px; font-weight: 600; color: var(--brand-blue); line-height: 1.1; }
  .person-role { font-size: 14px; color: var(--brand-green); margin-top: 2px; }
  .address { font-size: 14px; line-height: 18px; margin-top: 9px; }
  .contact-list { list-style: none; margin-top: 10px; font-size: 14px; }
  .contact-list li { display: flex; align-items: center; gap: 8px; height: 19.5px; }
  .contact-list svg { width: 12px; height: 12px; fill: var(--brand-blue); flex: none; }

  .partner-mark {
    position: absolute; left: 228px; top: 64px;
    width: 146px; height: 146px; border-radius: 50%;
    background: var(--navy);
    box-shadow: 0 0 0 3px var(--lime-deep), 0 0 0 4px var(--navy);
  }
  .partner-name {
    position: absolute; left: 0; right: 0; top: 222px;
    text-align: center; font-size: 34px; font-weight: 600; color: var(--navy);
    letter-spacing: -0.3px;
  }
</style>
</head>
<body>

<section class="card card-front" aria-label="Card front">
  <svg class="corner-swoosh" viewBox="0 0 600 342" aria-hidden="true">
    <path d="M0 0 H86 C70 34 30 44 0 80 Z" fill="var(--brand-green)"/>
    <path d="M0 80 C30 46 68 36 88 0" fill="none" stroke="var(--brand-blue)" stroke-width="4"/>
    <path d="M600 342 H514 C530 308 570 298 600 262 Z" fill="var(--brand-green)"/>
    <path d="M600 262 C570 296 532 306 512 342" fill="none" stroke="var(--brand-blue)" stroke-width="4"/>
  </svg>

  <div class="brand-lockup">
    <span class="brand-dot"></span>
    <span class="brand-name">BrightHarborTrade.example</span>
  </div>
  <p class="brand-tagline">Activities-Dining-Health-Beauty</p>

  <div class="contact-block">
    <h1 class="person-name">DANA WHITLOW</h1>
    <p class="person-role">CEO/FOUNDER</p>
    <p class="address">4870 West 63rd Avenue<br>Suite C207, Phoenix AZ 85731</p>
    <ul class="contact-list">
      <li><svg viewBox="0 0 24 24"><path d="M6.6 10.8a15 15 0 0 0 6.6 6.6l2.2-2.2c.3-.3.7-.4 1-.2 1.1.4 2.3.6 3.6.6.6 0 1 .4 1 1V20c0 .6-.4 1-1 1A17 17 0 0 1 3 4c0-.6.4-1 1-1h3.5c.6 0 1 .4 1 1 0 1.3.2 2.5.6 3.6.1.3 0 .7-.2 1z"/></svg>602 555 0148</li>
      <li><svg viewBox="0 0 24 24"><path d="M7 1h10a2 2 0 0 1 2 2v18a2 2 0 0 1-2 2H7a2 2 0 0 1-2-2V3a2 2 0 0 1 2-2zm0 3v14h10V4zm5 15.5a1.2 1.2 0 1 0 0 2.4 1.2 1.2 0 0 0 0-2.4z"/></svg>602 555 0193</li>
      <li><svg viewBox="0 0 24 24"><path d="M2 5h20v14H2zm2 2v.5l8 5 8-5V7zm0 2.8V17h16V9.8l-8 5z"/></svg>dana@brightharbortrade.example</li>
      <li><svg viewBox="0 0 24 24"><path d="M12 2a10 10 0 1 0 0 20 10 10 0 0 0 0-20zm6.9 6h-3a15 15 0 0 0-1.3-3.9A8 8 0 0 1 18.9 8zM12 4c.8 1.2 1.5 2.5 1.9 4h-3.8c.4-1.5 1.1-2.8 1.9-4zM4.3 14a8 8 0 0 1 0-4h3.4a16 16 0 0 0 0 4zm.8 2h3a15 15 0 0 0 1.3 3.9A8 8 0 0 1 5.1 16zm3-8h-3a8 8 0 0 1 4.3-3.9C8.8 5.3 8.4 6.6 8.1 8zM12 20c-.8-1.2-1.5-2.5-1.9-4h3.8c-.4 1.5-1.1 2.8-1.9 4zm2.3-6H9.7a14 14 0 0 1 0-4h4.6a14 14 0 0 1 0 4zm.3 5.9c.6-1.2 1-2.5 1.3-3.9h3a8 8 0 0 1-4.3 3.9zm1.7-5.9a16 16 0 0 0 0-4h3.4a8 8 0 0 1 0 4z"/></svg>www.brightharbortrade.example</li>
    </ul>
  </div>
</section>

<section class="card card-back" aria-label="Card back">
  <span class="partner-mark"></span>
  <p class="partner-name">Amber Ledge Partners</p>
</section>

</body>
</html>
```